Website development company website

ABOUT COMPANY
Hi everyone! We're a Melbourne, Australia website development company in a need of a website design that will make online store merchants want to engage our services.
We specialise exclusively in Torvista e-commerce platform (https://torvista-platform.example/). What distinguishes our business from competition is that rather than designing and building brand new websites, we offer development, support and maintenance services to established websites. Maintenance and Support are the keywords representing our business.
Our potential clients are people with broken, slow and underperforming Torvista installations who need assistance getting their websites up and making sales. Our website must pass the message that we can help, and provide quick means of making contact.
DESIGN
Overall, we're looking for a slick, clean, airy, conservative design. No need to do anything crazy, try to stick to what's "standard" in website design these days and make it easy on all of us. The website is unlikely to be updated too often so it needs to look attractive and fresh first time over and after a year, too.
Attached is our new logo, which you'll be able to take the basic idea from, the colors and fonts. Though, don't use the fonts from the logo in the website, stick to the standard widely supported fonts. Additional use of Google fonts is fine.
Don't overdo it with colors, stick to conservative basic color set and only use the colors from the log for accents like headings etc. Please, don't be tempted to use the blue and orange as background of whole blocks, other than perhaps footer. Thanks.
For the images used, I'd like to stay away from a design studio/digital agency feel and lean more towards professional support and maintenance services. I'm thinking images of content merchants doing their job. Something along the lines of "We'll be taking care of the website so that you only need to care about the business".
Some ideas I like:
http://www.plumframe-pics.example/detail/photo/portrait-of-confident-male-design-professional-royalty-free-image/572048163
http://www.plumframe-pics.example/detail/photo/designer-taking-picture-of-hat-high-res-stock-photography/839207514
http://www.plumframe-pics.example/detail/photo/woman-packaging-pottery-royalty-free-image/216684093
Images of colorful shopping bags and shopping carts are over the top and not serious enough. Instead of images matching Online Shopping, I'd try going more for Stability, Reliability, Performance.
Our existing website is http://www.bravuln.example. Please, don't take design ideas from it, but it will give you a picture of the structure of our new website and content that's going to be used initially.
If you could include a basic icon set to use throughout the website, that would be great. If the icons could match our logo (attached), it would be a big plus.
ALL PAGES
Every page must contain clearly visible phone number (1300 648 907) and a Contact Us Now button, which opens an AJAX driven popup form with Name, Email, Phone and Message to be sent through.
To start with, main menu items will be Torvista, Portfolio, Contact.
At the bottom of each page, please, include a newsletter subscription form with text Subscribe to Torvista Support and Security Updates.
For the footer, I'd like to see a logo strip with the following logos in grayscale (no need to link anywhere): Torvista, QRX, DataVane, NCB. You'll find the logos on Google Images.
Standard footer columns follow. Here, I'd like to see logos in color: Torvista Certified Developer, Torvista Ceritified Solution Provider. Again, the logos are on Google Images.
No social media logos/links necessary anywhere on the website.
...and then the copyright line.
FRONT PAGE
Large slider with images that would appeal to our target audience. Keywords here would be Torvista System Audit, Torvista Performance Optimisation, Torvista Website Emergency Recovery, Torvista Development Infrastructure Hosting. We'll have a static page created for each of these to link to.
In a corner of the slider, or on the edge, can I have an overlay with logos in color (same as footer): Torvista Certified Developer, Torvista Ceritified Solution Provider.
Underneath, a number of blocks, each with an image and teaser that we'll use to link to various pages throughout the website.
PORTFOLIO PAGE
I'm thinking a single long page with a block per client, which will contain project name, description from us and a testimonial from client. Also, each block will contain a single large screenshot. No gallery or slideshow is necessary here, just one image per project.
I'll leave the layout up to you, but try to put yourself in the shoes of a potential client reviewing our past work by simply scrolling down this one page.
CONTACT US PAGE
Separate page with the same form as above, phone number (1300 648 907), email address (support@kavreo.example), address (Suite 42, Level 3|8 Wattlebrook Lane|Fernvale Heights VIC 3999), and a grayscale Google Map.
CODING UP
Coding up into static HTML/CSS/JS is equally important as the design itself. We're a website development company, we'll be integrating the theme. We will spot any issues and we will point them out.
Coded up design must be fully responsive. Enough said.
To be able to create any content in future, we'd like one extra page coded up with samples of all themed elements, lists, forms, buttons, 2, 3, 4-column layout, alerts, icons, etc. This page does not need to be designed, only coded up.
The design will be integrated into Drupal using Twig. If possible at all, try to keep it in mind when designing and coding up, and make the integration into a Drupal theme easier for us.
GOOD LUCK!
That's it. Let me know if anything needs clarifying. So far I've had a great experience with ArtFlockly. I don't doubt some great designs will emerge. Clever ideas are highly appreciated, but also make it clear you've read and followed the points in this brief. Cheers, Tom

```html
<!DOCTYPE html>
<html lang="en">
<head>
<meta charset="utf-8">
<title>Kavreo E-Commerce — Torvista Development, Support &amp; Maintenance</title>
<link rel="stylesheet" href="https://fonts.googleapis.com/css2?family=Open+Sans:wght@300;400;600&family=Roboto+Condensed:wght@300;400;700&display=swap">
<style>
  :root{
    --navy:#0d3a6e;
    --orange:#e8821f;
    --ink:#1b2a3a;
    --text:#666a70;
    --grey-band:#e4e4e4;
    --light-band:#ededed;
    --footer:#232323;
    --footer-mark:#4a4a4a;
    --white:#ffffff;
  }
  *{box-sizing:border-box;margin:0;padding:0}
  h1,h2,h3,p{font-weight:400}
  html,body{width:1200px;height:2616px;overflow:hidden;background:var(--white)}
  body{position:relative;font-family:"Open Sans",Arial,sans-serif;color:var(--text)}
  section,header,footer{position:absolute;left:0;width:1200px}
  .abs{position:absolute}

  /* header */
  .site-header{top:0;height:105px;background:var(--white)}
  .brand{left:77px;top:22px;display:flex;align-items:center;gap:12px}
  .brand-mark{width:34px;height:34px;background:var(--orange)}
  .brand-name{font-family:"Roboto Condensed",Arial,sans-serif;font-weight:700;font-size:34px;line-height:1;color:var(--navy)}
  .main-nav a{position:absolute;top:28px;height:50px;line-height:50px;font-family:"Roboto Condensed",Arial,sans-serif;font-size:18px;color:#333;text-decoration:none;letter-spacing:.3px}
  .main-nav a.is-active{background:var(--navy);color:var(--white);width:94px;text-align:center}

  /* hero */
  .hero{top:105px;height:570px;background:linear-gradient(90deg,#8f9aa6 0%,#b7c0c9 30%,#d6dde3 55%,#e2e7eb 100%)}
  .hero-media{left:0;top:0;width:760px;height:570px}
  .hero-title{right:82px;top:112px;text-align:right;font-weight:300;font-size:38px;line-height:52px;color:var(--navy);letter-spacing:.3px}
  .btn-orange{background:var(--orange);color:var(--white);font-family:"Open Sans",Arial,sans-serif;text-align:center;text-decoration:none}
  .hero-cta{left:841px;top:345px;width:280px;height:73px;line-height:73px;font-size:27px;font-weight:400}

  /* call band */
  .call-band{top:675px;height:125px;background:var(--navy)}
  .call-text{left:192px;top:40px;font-family:"Roboto Condensed",Arial,sans-serif;font-size:35px;color:var(--white)}
  .call-icon{left:730px;top:33px;width:60px;height:60px}
  .call-number{left:813px;top:38px;font-family:"Roboto Condensed",Arial,sans-serif;font-weight:700;font-size:38px;color:var(--orange)}

  /* services */
  .services{top:800px;height:533px}
  .service{position:absolute;top:53px;width:340px}
  .service-icon{position:absolute;left:0;top:0;width:92px;height:92px;border-radius:50%;background:var(--orange)}
  .service-title{position:absolute;left:103px;top:4px;font-family:"Roboto Condensed",Arial,sans-serif;font-weight:400;font-size:25px;color:var(--navy)}
  .service-text{position:absolute;left:103px;top:44px;width:230px;font-size:15px;line-height:25px}

  .welcome-title{left:0;top:245px;width:1200px;text-align:center;font-family:"Roboto Condensed",Arial,sans-serif;font-weight:400;font-size:41px;color:var(--navy)}
  .welcome-title .accent,.work-title .accent{color:var(--orange)}
  .welcome-text{left:168px;top:314px;width:864px;text-align:center;font-size:15px;line-height:25px}
  .btn-outline{left:516px;top:412px;width:166px;height:53px;line-height:50px;border:1.5px solid var(--navy);text-align:center;font-family:"Roboto Condensed",Arial,sans-serif;font-size:22px;color:var(--navy);text-decoration:none}

  /* work */
  .our-work{top:1333px;height:467px;background:var(--grey-band)}
  .work-title{left:0;top:50px;width:1200px;text-align:center;font-family:"Roboto Condensed",Arial,sans-serif;font-weight:400;font-size:40px;color:var(--navy)}
  .work-card{position:absolute;top:116px;width:233px}
  .work-thumb{height:134px;background:var(--white);border:1px solid #d2d2d2;display:flex;align-items:center;justify-content:center;font-family:"Open Sans",Arial,sans-serif;font-weight:400;font-size:28px;color:#333}
  .work-name{margin-top:12px;font-weight:400;font-size:21px;color:var(--navy)}
  .work-quote{margin-top:4px;font-size:15px;line-height:25px}
  .work-client{font-size:15px;line-height:25px;color:var(--orange)}

  /* why */
  .why{top:1800px;height:380px;background:var(--white)}
  .why-art{left:157px;top:57px;width:366px;height:279px;background:linear-gradient(135deg,#f1a34f 0%,#1a4a80 55%,#0d3a6e 100%);border-radius:4px}
  .why-title{left:602px;top:60px;font-family:"Roboto Condensed",Arial,sans-serif;font-weight:400;font-size:35px;color:var(--navy)}
  .why-text{left:602px;top:124px;width:520px;font-size:15px;line-height:25px}
  .why-cta{left:600px;top:254px;width:199px;height:63px;line-height:63px;font-size:23px}

  /* newsletter */
  .newsletter{top:2180px;height:248px;background:var(--light-band)}
  .news-title{left:0;top:42px;width:1200px;text-align:center;font-weight:300;font-size:43px;color:var(--navy)}
  .news-sub{left:0;top:104px;width:1200px;text-align:center;font-size:19px;color:var(--orange)}
  .field{position:absolute;top:148px;height:47px;background:var(--white);border:1px solid #cfcfcf;padding-left:15px;line-height:45px;font-size:15px;color:#555}
  .news-btn{left:870px;top:148px;width:168px;height:47px;line-height:47px;background:var(--navy);color:var(--white);text-align:center;font-size:20px}

  /* footer */
  .site-footer{top:2428px;height:188px;background:var(--footer)}
  .tech-mark{position:absolute;top:44px;font-family:"Open Sans",Arial,sans-serif;font-weight:600;font-size:38px;color:var(--footer-mark);display:flex;align-items:center;gap:10px}
  .tech-mark .dot{width:28px;height:28px;background:var(--footer-mark)}
  .footer-rule{left:77px;top:135px;width:1046px;height:1px;background:#333}
  .copyright{left:0;top:150px;width:1200px;text-align:center;font-size:15px;color:#cfcfcf}
  .copyright b{color:var(--orange);font-weight:600}
</style>
</head>
<body>

<header class="site-header">
  <div class="brand abs">
    <span class="brand-mark"></span>
    <span class="brand-name">Kavreo E-Commerce</span>
  </div>
  <nav class="main-nav">
    <a class="is-active" href="#" style="left:525px">HOME</a>
    <a href="#" style="left:647px">ABOUT</a>
    <a href="#" style="left:757px">TORVISTA</a>
    <a href="#" style="left:895px">PORTFOLIO</a>
    <a href="#" style="left:1047px">CONTACT</a>
  </nav>
</header>

<section class="hero">
  <div class="hero-media abs" role="img" aria-label="Smiling merchant in a striped shirt working on a laptop in a bright office" style="background:linear-gradient(90deg,#7d8895,#a9b4bf 60%,rgba(214,221,227,0))"></div>
  <h1 class="hero-title abs">WE WILL BE TAKING CARE OF THE<br>WEBSITE SO THAT YOU ONLY<br>NEED TO CARE ABOUT<br>THE BUSINESS</h1>
  <a class="hero-cta btn-orange abs" href="#">CONTACT US NOW</a>
</section>

<section class="call-band">
  <p class="call-text abs">WE CAN HELP YOU CALL US TODAY</p>
  <svg class="call-icon abs" viewBox="0 0 60 60" aria-hidden="true">
    <circle cx="30" cy="30" r="28" fill="none" stroke="#e8821f" stroke-width="2"/>
    <path d="M22 18c2-1 4 0 5 2l2 4c1 2 0 3-1 4l-2 1c1 3 4 6 7 7l1-2c1-1 2-2 4-1l4 2c2 1 3 3 2 5-1 3-4 4-7 3-8-2-15-9-17-17-1-3 0-6 2-8z" fill="#e8821f"/>
  </svg>
  <p class="call-number abs">1300 648 907</p>
</section>

<section class="services">
  <div class="service" style="left:77px">
    <svg class="service-icon" viewBox="0 0 92 92" aria-hidden="true">
      <circle cx="46" cy="46" r="46" fill="#e8821f"/>
      <path d="M38 34l-12 12 12 12M54 34l12 12-12 12" fill="none" stroke="#fff" stroke-width="5" stroke-linecap="round" stroke-linejoin="round"/>
    </svg>
    <h3 class="service-title">DEVELOPMENT</h3>
    <p class="service-text">Lorem Ipsum is simply dummy text of the printing and typesetting industry.</p>
  </div>
  <div class="service" style="left:434px">
    <svg class="service-icon" viewBox="0 0 92 92" aria-hidden="true">
      <circle cx="46" cy="46" r="46" fill="#e8821f"/>
      <circle cx="46" cy="38" r="11" fill="#fff"/>
      <path d="M26 66c0-11 9-17 20-17s20 6 20 17z" fill="#fff"/>
    </svg>
    <h3 class="service-title">SUPPORT</h3>
    <p class="service-text">Lorem Ipsum is simply dummy text of the printing and typesetting industry.</p>
  </div>
  <div class="service" style="left:790px">
    <svg class="service-icon" viewBox="0 0 92 92" aria-hidden="true">
      <circle cx="46" cy="46" r="46" fill="#e8821f"/>
      <circle cx="40" cy="50" r="11" fill="none" stroke="#fff" stroke-width="6" stroke-dasharray="5 3"/>
      <circle cx="40" cy="50" r="4" fill="#fff"/>
      <circle cx="58" cy="34" r="7" fill="none" stroke="#fff" stroke-width="4" stroke-dasharray="4 2"/>
    </svg>
    <h3 class="service-title">MAINTENANCE</h3>
    <p class="service-text">Lorem Ipsum is simply dummy text of the printing and typesetting industry.</p>
  </div>

  <h2 class="welcome-title abs"><span class="accent">WELCOME TO</span> KAVREO E-COMMERCE</h2>
  <p class="welcome-text abs">Lorem Ipsum is simply dummy text of the printing and typesetting industry. Lorem Ipsum has been the industry's standard dummy text ever since the 1500s, when an unknown printer took a galley of type and scrambled it to make a type specimen book.</p>
  <a class="btn-outline abs" href="#">READ MORE</a>
</section>

<section class="our-work">
  <h2 class="work-title abs"><span class="accent">OUR</span> WORK</h2>
  <article class="work-card" style="left:77px">
    <div class="work-thumb">Stackhold</div>
    <h3 class="work-name">Holloway Stock</h3>
    <p class="work-quote">Bravuln are prompt and get the job done with the highest level of workmanship at a resonable price.</p>
    <p class="work-client">Reid Calloway, Stackhold</p>
  </article>
  <article class="work-card" style="left:347px">
    <div class="work-thumb">Dovrik</div>
    <h3 class="work-name">Dovrik</h3>
    <p class="work-quote">A fast solution is key when you are selling online. Bravuln are now our go to Torvista developers, very happy.</p>
    <p class="work-client">Oskar Vandermeer, Dovrik</p>
  </article>
  <article class="work-card" style="left:619px">
    <div class="work-thumb">Lumeya</div>
    <h3 class="work-name">Lumeya</h3>
    <p class="work-quote">Bravuln went above and beyond by delivering great work in excellent time frames.</p>
    <p class="work-client">Hamish Trell, Lumeya</p>
  </article>
  <article class="work-card" style="left:889px">
    <div class="work-thumb">Silk &amp; Seam</div>
    <h3 class="work-name">Holloway Stock</h3>
    <p class="work-quote">Bravuln are great developers whose concentration on detail does not compromise the delivery of work.</p>
    <p class="work-client">Lachlan Pryce, Silk &amp; Seam</p>
  </article>
</section>

<section class="why">
  <div class="why-art abs" role="img" aria-label="Illustration of a navy and orange shopping bag with a pointer cursor beside the Torvista platform mark"></div>
  <h2 class="why-title abs">WHY KAVREO E-COMMERCE ?</h2>
  <p class="why-text abs">Lorem Ipsum is simply dummy text of the printing and typesetting industry. Lorem Ipsum has been the industry's standard dummy text ever since the 1500s, when an unknown printer took a galley of type and scrambled it to make a type specimen book.</p>
  <a class="why-cta btn-orange abs" href="#">CONTACT US</a>
</section>

<section class="newsletter">
  <h2 class="news-title abs">NEWSLETTER</h2>
  <p class="news-sub abs">Subscribe to Torvista Support and Security Updates</p>
  <div class="field" style="left:162px;width:333px">Enter Name</div>
  <div class="field" style="left:516px;width:333px">Enter Emaill</div>
  <div class="news-btn abs">SUBSCRIBE</div>
</section>

<footer class="site-footer">
  <div class="tech-mark" style="left:150px"><span class="dot"></span>Torvista</div>
  <div class="tech-mark" style="left:465px">DataVane</div>
  <div class="tech-mark" style="left:700px">QRX</div>
  <div class="tech-mark" style="left:925px">NCB</div>
  <div class="footer-rule abs"></div>
  <p class="copyright abs">© <b>Kavreo E-commerce</b> - 2016. All Rights Reserved.</p>
</footer>

</body>
</html>
```